Business Card Design Project

After recently finishing a design project for the company logo using markbazaar, it's now time for a business card. Attached to this is the logo.

The requirements for the business card are pretty straightforward:

- A clean, uncomplicated look
- Consistent usage of fonts
- Designs for both single sided and double sided cards
- A modern layout with preferably space to refer to social media accounts and/or downloadable vcards through a qr code
- consistent application of the company colour scheme: red/white. Hex codes for exact colour can be provided

Thanks!

```html
<!DOCTYPE html>
<html lang="en">
<head>
<meta charset="utf-8">
<title>Oak Lane Staffing – Business Card</title>
<link rel="stylesheet" href="https://fonts.googleapis.com/css2?family=Open+Sans:wght@400;600;700&display=swap">
<style>
  :root {
    --brand-red: #e31e2a;
    --swoosh-grey: #8c8c8c;
    --ink: #231f20;
    --ink-soft: #3a3a3a;
    --card-white: #ffffff;
    --stage: #ececea;
    --divider: #9a9a9a;
  }
  * { margin: 0; padding: 0; box-sizing: border-box; }
  html, body {
    width: 960px; height: 1200px; overflow: hidden;
    background: var(--stage);
    font-family: "Open Sans", Arial, sans-serif;
    color: var(--ink);
  }
  .canvas { position: relative; width: 960px; height: 1200px; }
  .card {
    position: absolute; width: 840px; height: 480px;
    background: var(--card-white); border-radius: 30px; overflow: hidden;
    box-shadow: 0 6px 14px rgba(0,0,0,.18);
  }
  .card--front { left: 58px; top: 75px; }
  .card--back  { left: 60px; top: 637px; }

  .wordmark { position: absolute; display: flex; align-items: center; }
  .wordmark__square { background: var(--brand-red); flex: none; }
  .wordmark__name { font-weight: 600; color: var(--ink); white-space: nowrap; letter-spacing: -0.5px; }

  .card--front .wordmark { left: 37px; top: 100px; gap: 14px; }
  .card--front .wordmark__square { width: 30px; height: 30px; }
  .card--front .wordmark__name { font-size: 40px; }

  .divider { position: absolute; left: 514px; top: 87px; width: 1.5px; height: 118px; background: var(--divider); }

  .contact-person { position: absolute; left: 528px; top: 110px; }
  .contact-person__name { font-size: 24px; font-weight: 700; color: var(--ink-soft); line-height: 1; }
  .contact-person__role { font-size: 19px; color: var(--ink-soft); margin-top: 9px; line-height: 1; }
  .contact-person__phone { font-size: 19px; color: var(--ink-soft); margin-top: 13px; line-height: 1; }

  .contact-lines { position: absolute; left: 47px; top: 309px; font-size: 19px; color: var(--ink-soft); line-height: 28px; }
  .label { font-weight: 700; font-style: italic; }

  .card__art { position: absolute; inset: 0; }

  .address {
    position: absolute; left: 0; right: 0; top: 436px; text-align: center;
    font-size: 22px; color: #fff; padding-left: 36px;
  }

  .card--back .wordmark { left: 0; right: 0; top: 195px; justify-content: center; gap: 20px; }
  .card--back .wordmark__square { width: 46px; height: 46px; }
  .card--back .wordmark__name { font-size: 62px; }
</style>
</head>
<body>
<main class="canvas">
  <section class="card card--front" aria-label="Card front">
    <svg class="card__art" width="840" height="480" viewBox="0 0 840 480" aria-hidden="true">
      <path fill="var(--swoosh-grey)" d="M550,400 C680,392 790,340 840,255 L840,305 C790,362 690,396 550,400Z"/>
      <path fill="var(--brand-red)" d="M0,430 C60,398 150,380 250,385 C400,394 500,410 600,405 C720,398 800,350 840,315 L840,480 L0,480Z"/>
    </svg>

    <div class="wordmark">
      <span class="wordmark__square"></span>
      <span class="wordmark__name">Oak Lane Staffing</span>
    </div>

    <div class="divider"></div>

    <div class="contact-person">
      <p class="contact-person__name">Your Name</p>
      <p class="contact-person__role">Designation</p>
      <p class="contact-person__phone"><span class="label">t</span> : 123-123-1234</p>
    </div>

    <div class="contact-lines">
      <p><span class="label">e</span> : info@yourwebsite.com</p>
      <p><span class="label">w</span> : www.oaklanestaffing.com</p>
    </div>

    <p class="address">1234, Street Name, District, City, Country Code.</p>
  </section>

  <section class="card card--back" aria-label="Card back">
    <div class="wordmark">
      <span class="wordmark__square"></span>
      <span class="wordmark__name">Oak Lane Staffing</span>
    </div>
  </section>
</main>
</body>
</html>
```